We are a recruitment company based in Norwich/Cambridge England.
I have included our company logo which we want to remain the same.

What we are looking for is a new creative Business card which will really stand out!!

Contact Information for Business Card

Harriet Dunmore
email: Harriet@plavex.co.uk
Address: Brackwell House
Fenmoor Enterprise Park
Partridge Way
Norwich
QB9 3KX
Tel:01632 960418

```html
<!DOCTYPE html>
<html lang="en">
<head>
<meta charset="utf-8">
<title>Plavex Business Card</title>
<link rel="stylesheet" href="https://fonts.googleapis.com/css2?family=Montserrat:wght@500;600;700&family=Arimo:wght@400;700&display=swap">
<style>
  :root {
    --page-bg: #2a2a2b;
    --card-bg: #1f1f20;
    --card-glow: #262627;
    --deco: #2c2c2d;
    --brand-green: #7dc242;
    --brand-grey: #8e8b93;
    --text-grey: #a9a8ad;
    --line-green: #6fb236;
  }
  * { box-sizing: border-box; margin: 0; padding: 0; }
  html, body { width: 1200px; height: 1189px; overflow: hidden; }
  body {
    background: var(--page-bg);
    position: relative;
    font-family: "Arimo", Arial, sans-serif;
  }
  .card {
    position: absolute;
    left: 160px;
    width: 880px;
    height: 500px;
    border-radius: 30px;
    background: radial-gradient(ellipse at 60% 40%, var(--card-glow), var(--card-bg) 70%);
    overflow: hidden;
    box-shadow: 0 18px 40px rgba(0,0,0,0.45);
  }
  .card--front { top: 70px; }
  .card--back { top: 620px; }

  .deco-circle {
    position: absolute;
    border-radius: 50%;
    border: 70px solid var(--deco);
  }
  .card--front .deco-circle { width: 520px; height: 520px; left: 200px; top: -10px; }
  .card--back .deco-circle { width: 560px; height: 560px; left: 470px; top: -70px; }

  .brand {
    position: absolute;
    display: flex;
    align-items: center;
    gap: 18px;
  }
  .brand__dot {
    border-radius: 50%;
    background: var(--brand-green);
    flex: none;
  }
  .brand__name {
    font-family: "Montserrat", sans-serif;
    font-weight: 700;
    color: var(--brand-green);
    letter-spacing: 1px;
    line-height: 1;
  }
  .brand__tagline {
    font-family: "Montserrat", sans-serif;
    font-weight: 600;
    color: var(--brand-grey);
    letter-spacing: 5px;
    text-transform: none;
    margin-top: 8px;
  }
  .card--front .brand { left: 230px; top: 190px; }
  .card--front .brand__dot { width: 90px; height: 90px; }
  .card--front .brand__name { font-size: 78px; }
  .card--front .brand__tagline { font-size: 15px; }

  .card--back .brand { left: 70px; top: 60px; }
  .card--back .brand__dot { width: 74px; height: 74px; }
  .card--back .brand__name { font-size: 62px; }
  .card--back .brand__tagline { font-size: 13px; }

  .divider {
    position: absolute;
    left: 130px;
    right: 40px;
    top: 278px;
    height: 1.5px;
    background: var(--line-green);
  }
  .address {
    position: absolute;
    right: 50px;
    top: 205px;
    text-align: right;
    color: var(--text-grey);
    font-size: 19px;
    line-height: 1.3;
  }
  .person {
    position: absolute;
    left: 70px;
    top: 300px;
  }
  .person__name {
    font-weight: 700;
    font-size: 30px;
    color: var(--brand-green);
    letter-spacing: 0.5px;
  }
  .person__role {
    font-size: 21px;
    color: var(--text-grey);
    margin-top: 2px;
  }
  .person__rule {
    width: 260px;
    height: 1.5px;
    background: var(--line-green);
    margin: 8px 0 12px;
  }
  .contacts { list-style: none; }
  .contacts li {
    display: flex;
    align-items: center;
    gap: 12px;
    color: var(--text-grey);
    font-size: 21px;
    margin-bottom: 7px;
  }
  .contacts svg { width: 26px; height: 26px; flex: none; }
</style>
</head>
<body>

  <section class="card card--front" aria-label="Card front">
    <div class="deco-circle" aria-hidden="true"></div>
    <div class="brand">
      <span class="brand__dot" aria-hidden="true"></span>
      <div>
        <div class="brand__name">Plavex</div>
        <div class="brand__tagline">Technology Recruitment</div>
      </div>
    </div>
  </section>

  <section class="card card--back" aria-label="Card back">
    <div class="deco-circle" aria-hidden="true"></div>
    <div class="brand">
      <span class="brand__dot" aria-hidden="true"></span>
      <div>
        <div class="brand__name">Plavex</div>
        <div class="brand__tagline">Technology Recruitment</div>
      </div>
    </div>

    <div class="divider" aria-hidden="true"></div>

    <address class="address" style="font-style:normal">
      Brackwell House, Fenmoor Enterprise Park<br>
      Partridge Way, Norwich QB9 3KX
    </address>

    <div class="person">
      <div class="person__name">Harriet Dunmore</div>
      <div class="person__role">CEO</div>
      <div class="person__rule" aria-hidden="true"></div>
      <ul class="contacts">
        <li>
          <svg viewBox="0 0 26 26" aria-hidden="true"><circle cx="13" cy="13" r="11.5" fill="none" stroke="#7dc242" stroke-width="1.5"/><rect x="9" y="6.5" width="8" height="13" rx="1.5" fill="none" stroke="#7dc242" stroke-width="1.5"/><circle cx="13" cy="17" r="0.9" fill="#7dc242"/></svg>
          01632 960418
        </li>
        <li>
          <svg viewBox="0 0 26 26" aria-hidden="true"><circle cx="13" cy="13" r="11.5" fill="none" stroke="#7dc242" stroke-width="1.5"/><rect x="7" y="8.5" width="12" height="9" fill="#7dc242"/><path d="M7 8.5 L13 13.5 L19 8.5" fill="none" stroke="#1f1f20" stroke-width="1.3"/></svg>
          Harriet@plavex.co.uk
        </li>
        <li>
          <svg viewBox="0 0 26 26" aria-hidden="true"><circle cx="13" cy="13" r="11.5" fill="none" stroke="#7dc242" stroke-width="1.5"/><circle cx="13" cy="13" r="6.5" fill="none" stroke="#7dc242" stroke-width="1.3"/><ellipse cx="13" cy="13" rx="2.8" ry="6.5" fill="none" stroke="#7dc242" stroke-width="1.1"/><path d="M6.5 13 H19.5" stroke="#7dc242" stroke-width="1.1"/></svg>
          www.plavex.co.uk
        </li>
      </ul>
    </div>
  </section>

</body>
</html>
```